Card design for orthopaedic surgeons working as The Brightwater Joint Centre

Business cards, letterhead

Colors

Designer to choose colors to be used in the design.

Requirements
Must have
• Late addition.
• Cards letterhead must have logos of
• Crestmoor Lindell College of Surgeons
• Varenwood Bone Health Association
Nice to have
• Back of card to have space for appointment time to be added by hand and some blank space for writing incidental other notes.

```html
<!DOCTYPE html>
<html lang="en">
<head>
<meta charset="utf-8">
<title>The Brightwater Joint Centre – Business Card</title>
<link rel="stylesheet" href="https://fonts.googleapis.com/css2?family=Montserrat:wght@400;500&display=swap">
<style>
  :root {
    --backdrop: #c4c4c4;
    --card: #ffffff;
    --brand-blue: #00aeef;
    --ink: #222222;
    --rule: #6e6e6e;
    --badge-warm: #c9a45a;
    --badge-cool: #9aa4b0;
  }
  * { box-sizing: border-box; margin: 0; padding: 0; }
  html, body {
    width: 1200px; height: 1000px; overflow: hidden;
    background: var(--backdrop);
    font-family: "Montserrat", Arial, sans-serif;
    color: var(--ink);
  }
  .canvas { position: relative; width: 1200px; height: 1000px; }
  .card {
    position: absolute; left: 262px; width: 674px; height: 374px;
    background: var(--card); border-radius: 32px; overflow: hidden;
  }
  .card--front { top: 82px; }
  .card--back { top: 545px; }

  .front__band {
    position: absolute; left: 0; top: 0; width: 100%; height: 161px;
    background: var(--brand-blue);
    display: flex; align-items: center; justify-content: center;
    padding-top: 30px;
  }
  .brand-name { font-weight: 400; letter-spacing: -0.5px; white-space: nowrap; }
  .front__band .brand-name { color: #ffffff; font-size: 36px; }

  .appointment { position: absolute; left: 74px; top: 175px; width: 260px; }
  .appointment__label { font-size: 20px; text-align: center; letter-spacing: 0.5px; }
  .appointment__box { margin-top: 8px; height: 37px; border: 1px solid var(--rule); }

  .badge { position: absolute; }
  .badge--college { left: 406px; top: 230px; width: 102px; height: 120px; }
  .badge--association { left: 528px; top: 240px; width: 113px; height: 110px; }

  .back__brand { position: absolute; left: 36px; top: 70px; }
  .back__brand .brand-name { color: var(--brand-blue); font-size: 28px; }

  .person { position: absolute; left: 36px; top: 222px; }
  .person__name { font-size: 23px; font-weight: 400; }
  .person__role { font-size: 19px; margin-top: 2px; }
  .social { position: absolute; left: 36px; top: 305px; display: flex; align-items: center; gap: 10px; font-size: 19px; }
  .social__dot { width: 28px; height: 28px; border-radius: 50%; background: var(--brand-blue); }

  .divider { position: absolute; left: 322px; top: 218px; width: 1px; height: 117px; background: var(--rule); }

  .contact { position: absolute; left: 361px; top: 218px; width: 290px; list-style: none; }
  .contact li { display: flex; align-items: center; gap: 9px; height: 30px; font-size: 17px; white-space: nowrap; }
  .contact svg { width: 26px; height: 26px; flex: none; }
</style>
</head>
<body>
<main class="canvas">
  <section class="card card--front" aria-label="Card front">
    <div class="front__band">
      <span class="brand-name">The Brightwater Joint Centre</span>
    </div>
    <div class="appointment">
      <p class="appointment__label">Appointment Time</p>
      <div class="appointment__box"></div>
    </div>
    <svg class="badge badge--college" viewBox="0 0 102 120" role="img" aria-label="Crestmoor Lindell College of Surgeons badge">
      <rect x="0" y="0" width="102" height="120" rx="10" fill="var(--badge-warm)"/>
    </svg>
    <svg class="badge badge--association" viewBox="0 0 113 110" role="img" aria-label="Varenwood Bone Health Association badge">
      <rect x="0" y="0" width="113" height="110" rx="10" fill="var(--badge-cool)"/>
    </svg>
  </section>

  <section class="card card--back" aria-label="Card back">
    <div class="back__brand"><span class="brand-name">The Brightwater Joint Centre</span></div>
    <div class="person">
      <p class="person__name">Name</p>
      <p class="person__role">Designation</p>
    </div>
    <div class="social"><span class="social__dot"></span><span>bw_joint</span></div>
    <div class="divider"></div>
    <ul class="contact">
      <li>
        <svg viewBox="0 0 26 26"><circle cx="13" cy="13" r="13" fill="var(--brand-blue)"/><path d="M13 6a5 5 0 0 0-5 5c0 4 5 9 5 9s5-5 5-9a5 5 0 0 0-5-5z" fill="#fff"/><circle cx="13" cy="11" r="1.8" fill="var(--brand-blue)"/></svg>
        <span>Address</span>
      </li>
      <li>
        <svg viewBox="0 0 26 26"><circle cx="13" cy="13" r="13" fill="var(--brand-blue)"/><path d="M9 6.5l2.5 3-1.5 2a8 8 0 0 0 4.5 4.5l2-1.5 3 2.5-1.5 2.5c-5 0-10.5-5.5-10.5-10.5z" fill="#fff"/></svg>
        <span>555-0142-88</span>
      </li>
      <li>
        <svg viewBox="0 0 26 26"><circle cx="13" cy="13" r="13" fill="var(--brand-blue)"/><rect x="6.5" y="8.5" width="13" height="9" rx="1" fill="none" stroke="#fff" stroke-width="1.4"/><path d="M6.8 9l6.2 5 6.2-5" fill="none" stroke="#fff" stroke-width="1.4"/></svg>
        <span>info@bwjoint.example</span>
      </li>
      <li>
        <svg viewBox="0 0 26 26"><circle cx="13" cy="13" r="13" fill="var(--brand-blue)"/><circle cx="13" cy="13" r="7" fill="none" stroke="#fff" stroke-width="1.3"/><ellipse cx="13" cy="13" rx="3" ry="7" fill="none" stroke="#fff" stroke-width="1.3"/><path d="M6 13h14" stroke="#fff" stroke-width="1.3"/></svg>
        <span>www.bwjoint.example</span>
      </li>
    </ul>
  </section>
</main>
</body>
</html>
```